Public Relations Agency Seeks Wordpress Design and Coding

TRELVOX Studio is a public relations agency specializing in media relations, public affairs and marketing communication.

The site should display the following visual characteristics: professionalism, trustworthiness, high-tech focus, clear and concise design.

The desired colors are royal blue, gray and hints of red.

Design look/feel inspired by this site: http://brightpathgatherings.example/

Specifications:

1. Navigation/Pages/Index:

HOME

ABOUT US

SERVICES

NEWS

CONTACT

---

2. Functionality of/content for each page:

- Home
o Dominant photo (professional, edgy, innovative)
o Simple, straightforward access to/from “Home” from other pages
o Includes logo (attached) and tagline "Unleash the power of communication"
o Direct link to “CONTACT”
o Links to social media accounts: Facebook, Twitter, LinkedIn

- About Us

o Company profile blurb
o President’s photo with short bio

- Services
o Public Relations
 Strategic communication
 Brand and reputation management
 Community relations
o Media Relations
 News coverage and contacts
 Media training and interview skills
 Crisis communications
o Congressional Affairs
 Public affairs
 Public policy
 Legislative strategy
o Mass Communication
 Speechwriting
 Presentation creation
 Social media
o Marketing Communications
 Business collateral material
 Promotional campaigns
 Special events and tradeshows

- News
o Blog-like page to post information and/or share news from other sites

- Contact
o Standard “Contact Us” form (Name, Email, Phone, Message)
o Direct Contact
 (407) 555-0164
 Marisol@TRELVOXstudio.example

Target Market(s)

Small to large businesses specializing in high technology, defense/military, medicine/healthcare, and wide array of professional services.

Industry/Entity Type

Marketing

Font styles to use
Serif
Sans Serif

Colors
0555a3
ec2027
edf3f7

Requirements
Must have
• -- Project reqires DESIGN - and - fully CODED.

-- Strong SEO

-- Optimized for mobile viewing

Thank you!

```html
<!DOCTYPE html>
<html lang="en">
<head>
<meta charset="utf-8">
<title>TRELVOX Studio — Unleash the Power of Communication</title>
<link rel="stylesheet" href="https://fonts.googleapis.com/css2?family=Roboto+Slab:wght@400;700&family=Roboto:wght@400;500&display=swap">
<style>
:root{
  --red:#c1291e;
  --navy:#03183a;
  --blue:#0555a3;
  --ink:#2b2b2b;
  --light:#f4f4f4;
  --footer:#151515;
  --white:#fff;
}
*{box-sizing:border-box;margin:0;padding:0}
html,body{width:1200px;height:2261px;overflow:hidden}
body{font-family:"Roboto",Arial,sans-serif;color:var(--ink);background:var(--white);position:relative}
.slab{font-family:"Roboto Slab",Georgia,serif}

/* header */
.site-header{position:absolute;top:0;left:0;width:1200px;height:98px;background:var(--white)}
.brand{position:absolute;left:173px;top:34px;display:flex;align-items:center;gap:10px;font-weight:500;font-size:26px;color:#555;letter-spacing:1px}
.brand-dot{width:10px;height:10px;background:var(--red)}
.main-nav{position:absolute;top:44px;left:0;font-size:14px;color:#333}
.main-nav a{position:absolute;white-space:nowrap;color:inherit;text-decoration:none}
.main-nav a.active{color:var(--red);border-bottom:2px solid var(--red);padding-bottom:4px}
.social-ring{position:absolute;width:32px;height:32px;border-radius:50%;border:1px solid #888}
.social-ring.first{border-color:var(--red)}

/* hero */
.hero{position:absolute;top:98px;left:0;width:1200px;height:547px;
  background:linear-gradient(160deg,#9fb4c8 0%,#c3a08b 35%,#8d6b5a 60%,#4a5466 100%)}
.hero-title{position:absolute;top:262px;width:1200px;text-align:center;color:var(--white);font-family:"Roboto Slab",Georgia,serif;font-weight:700;font-size:33px;white-space:nowrap;text-shadow:0 2px 4px rgba(0,0,0,.5)}
.hero-btn{position:absolute;left:490px;top:336px;width:220px;height:63px;background:var(--red);color:var(--white);font-family:"Roboto Slab",Georgia,serif;font-weight:700;font-size:21px;white-space:nowrap;display:flex;align-items:center;justify-content:space-between;padding:0 18px;box-shadow:0 2px 4px rgba(0,0,0,.3)}
.hero-dots{position:absolute;left:1144px;top:240px;display:flex;flex-direction:column;gap:6px}
.hero-dots i{width:12px;height:12px;border-radius:50%;background:var(--white)}
.hero-dots i.on{background:#e31e24}

/* soft bands */
.soft-band{position:absolute;left:0;width:1200px;background:linear-gradient(120deg,#f3dcdc 0%,#ead0d6 40%,#d6c2d2 75%,#c8b6c8 100%)}
.section-title{position:absolute;width:1200px;text-align:center;font-family:"Roboto Slab",Georgia,serif;font-weight:400;font-size:34px;color:var(--red)}

/* about */
.about{top:645px;height:344px}
.president-photo{position:absolute;left:175px;top:97px;width:180px;height:180px;border-radius:50%;border:4px solid var(--white);box-shadow:0 0 0 2px #555;background:linear-gradient(180deg,#d9c08a 0%,#e5c3a8 55%,#b83a33 100%)}
.about-text{position:absolute;left:384px;top:107px;width:643px;font-size:15.5px;line-height:32.7px;text-align:justify;color:#333}

/* services */
.services{position:absolute;top:989px;left:0;width:1200px;height:448px;background:linear-gradient(135deg,#012253 0%,#0b4d95 30%,#032455 55%,#0a4f9c 80%,#021a3c 100%)}
.services .section-title{color:var(--white);top:36px}
.service{position:absolute;top:128px;width:260px;text-align:center;color:var(--white)}
.service-icon{width:134px;height:134px;margin:0 auto;border-radius:50%;background:var(--red);border:2px solid var(--white);display:flex;align-items:center;justify-content:center}
.service h3{font-family:"Roboto Slab",Georgia,serif;font-weight:400;font-size:16px;margin-top:14px;letter-spacing:.3px;white-space:nowrap}
.service p{font-size:11.3px;line-height:20px;margin-top:12px;text-align:left}

/* news */
.news{top:1437px;height:346px}
.news-card{position:absolute;top:110px;height:156px;background:var(--white);box-shadow:0 1px 4px rgba(0,0,0,.2)}
.news-date{position:absolute;left:14px;top:32px;width:80px;height:84px;background:var(--light);border:1px solid #ddd;text-align:center}
.news-date b{display:block;height:50px;line-height:50px;font-size:27px;background:var(--white);font-weight:500}
.news-date span{display:block;line-height:32px;font-size:15px;color:#777;background:#e6e6e6}
.news-card h4{position:absolute;left:113px;top:26px;font-weight:500;font-size:19px;color:#1b3f8e;white-space:nowrap}
.news-card p{position:absolute;left:113px;top:57px;right:14px;font-size:11.4px;line-height:19px;text-align:justify;color:#333}

/* testimonial */
.testimonial{position:absolute;top:1783px;left:0;width:1200px;height:284px;background:var(--white);text-align:center}
.quote-badge{position:absolute;left:568px;top:36px;width:64px;height:64px}
.quote-text{position:absolute;top:116px;width:1200px;font-size:21.5px;line-height:35px;color:#222}
.quote-author{position:absolute;top:200px;width:1200px;font-size:16px;color:var(--red)}
.quote-dots{position:absolute;top:239px;left:554px;display:flex;gap:6px}
.quote-dots i{width:10px;height:10px;border-radius:50%;border:1px solid #777}
.quote-dots i.on{background:var(--red);border-color:var(--red)}

/* footer */
.site-footer{position:absolute;top:2067px;left:0;width:1200px;height:194px;background:var(--footer);color:#ddd}
.footer-brand{position:absolute;left:176px;top:60px;display:flex;align-items:center;gap:8px;font-weight:500;font-size:22px;color:#777;letter-spacing:1px}
.footer-brand .brand-dot{width:8px;height:8px}
.footer-ring{position:absolute;top:51px;width:54px;height:54px;border-radius:50%;border:1px solid #888}
.footer-contact{position:absolute;right:170px;top:54px;text-align:right;font-size:14.5px;line-height:24px}
.footer-contact div{display:flex;align-items:center;justify-content:flex-end;gap:8px}
.copyright{position:absolute;top:146px;width:1200px;text-align:center;font-size:12px;color:#ddd}
</style>
</head>
<body>

<header class="site-header">
  <div class="brand">TRELVOX Studio<span class="brand-dot"></span></div>
  <nav class="main-nav">
    <a class="active" style="left:482px">HOME</a>
    <a style="left:553px">ABOUT US</a>
    <a style="left:650px">SERVICES</a>
    <a style="left:743px">NEWS</a>
    <a style="left:813px">CONTACT US</a>
  </nav>
  <span class="social-ring first" style="left:919px;top:38px" aria-label="Social profile link"></span>
  <span class="social-ring" style="left:958px;top:38px" aria-label="Social profile link"></span>
  <span class="social-ring" style="left:996px;top:38px" aria-label="Social profile link"></span>
</header>

<section class="hero" role="img" aria-label="Group of smiling young friends in sunglasses looking at a tablet outdoors">
  <h1 class="hero-title">UNLEASH THE POWER OF COMMUNICATION</h1>
  <a class="hero-btn">VIEW MORE
    <svg width="32" height="32" viewBox="0 0 32 32"><circle cx="16" cy="16" r="14" fill="none" stroke="#fff" stroke-width="2.5"/><path d="M13 10l6 6-6 6" fill="none" stroke="#fff" stroke-width="2.5"/></svg>
  </a>
  <div class="hero-dots"><i class="on"></i><i></i><i></i><i></i><i></i></div>
</section>

<section class="soft-band about">
  <h2 class="section-title" style="top:30px">ABOUT US</h2>
  <div class="president-photo" role="img" aria-label="Portrait of the agency president"></div>
  <p class="about-text">Lorem Ipsum is simply dummy text of the printing and typesetting industry. Lorem Ipsum has been the industry's standard dummy text ever since the 1500s, when an unknown printer took a galley of type and scrambled it to make a type specimen book. It has survived not only five centuries, but also the leap into electronic typesetting, remaining essentially unchanged. It was popularised in the 1960s with the release of Letraset sheets containing</p>
</section>

<section class="services">
  <h2 class="section-title">SERVICES</h2>
  <div class="service" style="left:172px">
    <div class="service-icon"><svg width="56" height="56" viewBox="0 0 56 56" fill="#fff"><circle cx="28" cy="20" r="11"/><path d="M6 26c4 10 10 18 22 22 12-4 18-12 22-22l-5-2c-3 8-8 14-17 17-9-3-14-9-17-17z"/></svg></div>
    <h3>MEDIA RELATIONS</h3>
    <p>Lorem Ipsum is simply dummy text of the printing and typesetting industry. Lorem Ipsum has been the industry's standard dummy text ever</p>
  </div>
  <div class="service" style="left:470px">
    <div class="service-icon"><svg width="64" height="56" viewBox="0 0 64 56" fill="#fff"><circle cx="14" cy="18" r="6"/><circle cx="32" cy="14" r="7"/><circle cx="50" cy="18" r="6"/><path d="M4 40c0-8 4-13 10-13s10 5 10 13zM20 40c0-10 5-16 12-16s12 6 12 16zM40 40c0-8 4-13 10-13s10 5 10 13z"/></svg></div>
    <h3>PUBLIC AFFAIRS</h3>
    <p>Lorem Ipsum is simply dummy text of the printing and typesetting industry. Lorem Ipsum has been the industry's standard dummy text ever</p>
  </div>
  <div class="service" style="left:767px">
    <div class="service-icon"><svg width="56" height="56" viewBox="0 0 56 56"><circle cx="28" cy="28" r="20" fill="none" stroke="#fff" stroke-width="5"/><circle cx="28" cy="28" r="8" fill="#fff"/></svg></div>
    <h3>MARKETING COMMUNICATION</h3>
    <p>Lorem Ipsum is simply dummy text of the printing and typesetting industry. Lorem Ipsum has been the industry's standard dummy text ever</p>
  </div>
</section>

<section class="soft-band news">
  <h2 class="section-title" style="top:34px">LATEST NEWS</h2>
  <article class="news-card" style="left:170px;width:409px">
    <div class="news-date"><b>20</b><span>mar</span></div>
    <h4>NEWS HEADLINE HERE</h4>
    <p>Lorem Ipsum is simply dummy text of the printing and typesetting industry. Lorem Ipsum has been the industry's standard dummy text ever since the 1500s, when an unknown printer took a galley of type and</p>
  </article>
  <article class="news-card" style="left:603px;width:427px">
    <div class="news-date"><b>20</b><span>mar</span></div>
    <h4>NEWS HEADLINE HERE</h4>
    <p>Lorem Ipsum is simply dummy text of the printing and typesetting industry. Lorem Ipsum has been the industry's standard dummy text ever since the 1500s, when an unknown printer took a galley of type and</p>
  </article>
</section>

<section class="testimonial">
  <svg class="quote-badge" viewBox="0 0 64 64"><circle cx="32" cy="32" r="32" fill="#2c2c2c"/><path d="M20 40v-9c0-6 3-10 8-11v4c-2 1-3 3-3 6h3v10zM35 40v-9c0-6 3-10 8-11v4c-2 1-3 3-3 6h3v10z" fill="#fff"/></svg>
  <p class="quote-text">“To take a trivial example, which of us ever undertakes laborious physical exercise,<br>except to obtain some advantage from it? But who has any right to find.”</p>
  <p class="quote-author">Dana Whitlock</p>
  <div class="quote-dots"><i></i><i></i><i class="on"></i><i></i><i></i><i></i></div>
</section>

<footer class="site-footer">
  <div class="footer-brand">TRELVOX Studio<span class="brand-dot"></span></div>
  <span class="footer-ring" style="left:495px" aria-label="Social profile link"></span>
  <span class="footer-ring" style="left:573px" aria-label="Social profile link"></span>
  <span class="footer-ring" style="left:653px" aria-label="Social profile link"></span>
  <div class="footer-contact">
    <div><svg width="16" height="16" viewBox="0 0 16 16"><circle cx="8" cy="8" r="7" fill="none" stroke="#e31e24" stroke-width="1.5"/><path d="M5 4l2 2-1 1c1 2 2 3 3 3l1-1 2 2-1 1c-3 0-7-4-7-7z" fill="#e31e24"/></svg>+971-52-5550178</div>
    <div><svg width="14" height="10" viewBox="0 0 14 10"><rect width="14" height="10" fill="#e31e24"/><path d="M0 0l7 5 7-5" fill="none" stroke="#151515" stroke-width="1.2"/></svg>info@trelvoxstudio.example</div>
  </div>
  <p class="copyright">Copyright © 2014 trelvoxstudio, All rights reserved.</p>
</footer>

</body>
</html>
```